We’re a real estate firm that has landed a big builder in a neighboring state. Our branding needs...

We are a real estate firm who represents various builders along with doing resale here in Oregon. Our firm is growing to represent a big builder in Washington State and we’ll have another 40 brokers on our team. We need rebranding. As in, a new logo ( the house logo we have now looks cartoonish, hate it). We need new cards, something to really stand out. I’ve been thinking of using those NFC cards from ZEP or the ones with the seam color. I likely want two or three designs, a darker (as in a background color of black or grey) , a light one ( again I mean background color) and a credit card style (either plastic w an embossed name/number on front, or metal ). I’m thinking dark background for cc, or silver if it’s metal. That’s my thoughts, but you are the artists, so maybe you have an idea I haven’t considered. Our colors were black and red, but we don’t have to stick to that. Just nothing too busy. Oh, and we are typically representing the local, higher quality builders in our area (just below custom), but not national. Subdivisions are near the Kell Varney, Brisco, and Thornfield Crest sites. We are super excited, but without a lot of time to change the “look” of our brokerage. So I’ll be deciding and moving forward within 24 hours tops. Our name is Real Estate Summit Alliance ( we cant change the name because of timeline and business license) Thank you!

Industry/Entity Type

Real Estate

Contact Information for Business Card

The usual. Name of firm. Name of cardholder. Contact info.

Font styles to use
Serif
Sans Serif

Colors

Designer to choose colors to be used in the design.

Requirements
Must have
• A sleek or simple look. I included photos of cards with stylistic attributes we like. Thank you
Nice to have
• We really like the black backgrounds. With foil or embossed detail. We also like the black on black. Matte black card with raised shiny black detail. But still eye catching.
Should not have
• No ornate or busy looking style. We don’t want anything cluttered.

```html
<!DOCTYPE html>
<html lang="en">
<head>
<meta charset="utf-8">
<title>Real Estate Summit Alliance – Business Cards</title>
<link href="https://fonts.googleapis.com/css2?family=Open+Sans:wght@400;600;700&display=swap" rel="stylesheet">
<style>
  :root {
    --stage: #e6e6e6;
    --brand-red: #c81e1e;
    --card-white: #ffffff;
    --ink: #3a3a3a;
    --ink-soft: #555555;
    --house-grey: #ececee;
  }
  * { margin: 0; padding: 0; box-sizing: border-box; }
  html, body { width: 1200px; height: 900px; overflow: hidden; }
  body {
    background: var(--stage);
    font-family: "Open Sans", Arial, sans-serif;
    position: relative;
  }
  .card {
    position: absolute;
    top: 313px;
    width: 490px;
    height: 280px;
    border-radius: 26px;
    overflow: hidden;
    box-shadow: 0 10px 24px rgba(0,0,0,0.14);
  }
  .card--front { left: 80px; background: var(--brand-red); }
  .card--back { left: 630px; background: var(--card-white); }

  .front-wordmark {
    position: absolute;
    inset: 0;
    display: flex;
    flex-direction: column;
    align-items: center;
    justify-content: center;
    color: var(--card-white);
    font-weight: 700;
    text-align: center;
  }
  .front-wordmark__short { font-size: 62px; letter-spacing: 4px; line-height: 1; }
  .front-wordmark__full { font-size: 19px; letter-spacing: 3px; text-transform: uppercase; margin-top: 12px; }

  .house-roof, .house-wall { position: absolute; display: block; }
  .house-roof { top: 0; right: 0; }

  .back-wordmark {
    position: absolute;
    left: 36px;
    top: 84px;
    font-size: 48px;
    font-weight: 700;
    letter-spacing: 3px;
    color: var(--brand-red);
    line-height: 1;
  }
  .holder { position: absolute; left: 38px; top: 150px; }
  .holder__name { font-size: 17px; font-weight: 700; color: var(--brand-red); text-transform: uppercase; letter-spacing: 0.5px; line-height: 1.1; }
  .holder__role { font-size: 14px; color: var(--ink-soft); line-height: 1.2; }
  .contact-list { list-style: none; margin-top: 8px; }
  .contact-list li {
    display: flex; align-items: center; gap: 8px;
    font-size: 14px; color: var(--ink); line-height: 1.45;
  }
  .contact-list svg { width: 11px; height: 11px; flex: none; fill: var(--brand-red); }
  .address {
    position: absolute; right: 30px; top: 150px;
    text-align: right; font-size: 14px; color: var(--ink); line-height: 1.4;
  }
</style>
</head>
<body>
  <section class="card card--front" aria-label="Card front">
    <div class="front-wordmark">
      <span class="front-wordmark__short">RESA</span>
      <span class="front-wordmark__full">Real Estate Summit Alliance</span>
    </div>
  </section>

  <section class="card card--back" aria-label="Card back">
    <svg class="house-roof" width="490" height="280" viewBox="0 0 490 280" aria-hidden="true">
      <polygon points="270,0 490,0 490,60 300,60" fill="var(--house-grey)"/>
      <rect x="360" y="90" width="130" height="70" fill="var(--house-grey)"/>
    </svg>

    <div class="back-wordmark">RESA</div>

    <div class="holder">
      <p class="holder__name">Marcus Hale</p>
      <p class="holder__role">Managing Director</p>
      <ul class="contact-list">
        <li><svg viewBox="0 0 12 12"><path d="M1 4c0-2 2-3 5-3s5 1 5 3l-2 1-1-1H4L3 5 1 4zM3 6h6l1 5H2z"/></svg>503-555 0142</li>
        <li><svg viewBox="0 0 12 12"><path d="M3 0h6v12H3zM4 1.5v8h4v-8z"/></svg>503-555 0187</li>
        <li><svg viewBox="0 0 12 12"><path d="M0 2h12v8H0zM1 3l5 4 5-4v-.2H1z"/></svg>info@resa-example.com</li>
        <li><svg viewBox="0 0 12 12"><circle cx="6" cy="6" r="6"/></svg>www.resa-example.com</li>
      </ul>
    </div>

    <address class="address" style="font-style:normal">
      12345, Address Goes Here<br>Country Name, 123456
    </address>
  </section>
</body>
</html>
```